Basic business card

use my newly created logo - and the phrases (Lower Cost of Test & Accelarated New Product Introduction) - and my new email domain / ID - use at conferences / tradeshows

Industry/Entity Type

semiconductor

Contact Information for Business Card

Daniel K Forde, Owner, communicate via Logo - Lower COT - Cost of Test, Accelerated NPI - New Product Introduction, phone +1 555 613 0946, Chandler, Arizona, USA, daniel.forde@qal-vub.com

Font styles to use
Sans Serif

Requirements
Nice to have
• re-use my logo created via Pixel Harbor last August (#7315926)

```html
<!DOCTYPE html>
<html lang="en">
<head>
<meta charset="utf-8">
<title>QAL-VUB Business Card</title>
<link href="https://fonts.googleapis.com/css2?family=Open+Sans:wght@400;600;700&display=swap" rel="stylesheet">
<style>
  :root {
    --stage: #242424;
    --card: #1f1f23;
    --edge: #7cc242;
    --band: #7cc242;
    --slate: #4a5268;
    --silver: #9aa3b2;
    --orange: #f7941d;
    --blue: #1b75bc;
    --white: #ffffff;
  }
  * { margin: 0; padding: 0; box-sizing: border-box; }
  html, body { width: 1200px; height: 780px; overflow: hidden; }
  body {
    background: var(--stage);
    font-family: "Open Sans", Arial, sans-serif;
    display: flex;
    align-items: center;
    justify-content: center;
    gap: 30px;
  }
  .card {
    position: relative;
    width: 560px;
    height: 320px;
    background: var(--card);
    border-radius: 22px;
    box-shadow: 0 0 0 3px var(--edge), 0 18px 30px rgba(0,0,0,.55);
    overflow: hidden;
  }
  /* Logo side */
  .card-back { display: flex; align-items: center; justify-content: center; gap: 16px; }
  .brand-mark { width: 26px; height: 26px; background: var(--slate); }
  .brand-name {
    font-size: 62px; font-weight: 600; color: var(--silver); letter-spacing: 2px;
  }
  /* Contact side */
  .brand-block {
    position: absolute; left: 40px; top: 70px; width: 230px; height: 150px;
    display: flex; align-items: center; gap: 12px;
  }
  .brand-block .brand-mark { width: 20px; height: 20px; }
  .brand-block .brand-name { font-size: 40px; letter-spacing: 1px; color: var(--slate); }
  .divider {
    position: absolute; left: 292px; top: 52px; width: 2px; height: 170px; background: var(--white);
  }
  .person { position: absolute; left: 318px; top: 58px; }
  .person-name { font-size: 27px; font-weight: 700; line-height: 1.1; white-space: nowrap; }
  .person-name .first { color: var(--orange); }
  .person-name .last { color: var(--blue); }
  .person-title { color: var(--white); font-size: 14px; font-weight: 600; margin-top: 4px; }
  .contacts { list-style: none; margin-top: 26px; }
  .contacts li {
    display: flex; align-items: center; gap: 10px;
    color: var(--white); font-size: 14px; line-height: 22px;
  }
  .contacts svg { width: 14px; height: 14px; flex: none; }
  .address-band {
    position: absolute; left: 0; right: 0; bottom: 18px; height: 40px;
    background: var(--band);
    display: flex; align-items: center; justify-content: center;
    color: var(--white); font-size: 15px; font-weight: 600; letter-spacing: .3px;
  }
</style>
</head>
<body>

<section class="card card-back">
  <span class="brand-mark"></span>
  <span class="brand-name">QAL-VUB</span>
</section>

<section class="card card-front">
  <div class="brand-block">
    <span class="brand-mark"></span>
    <span class="brand-name">QAL-VUB</span>
  </div>

  <div class="divider"></div>

  <div class="person">
    <p class="person-name"><span class="first">Irena</span> <span class="last">Kovalska</span></p>
    <p class="person-title">Managing Director</p>
    <ul class="contacts">
      <li>
        <svg viewBox="0 0 24 24" aria-hidden="true"><path fill="#f7941d" d="M6.6 10.8a15.1 15.1 0 0 0 6.6 6.6l2.2-2.2a1 1 0 0 1 1-.25 11.4 11.4 0 0 0 3.6.57 1 1 0 0 1 1 1V20a1 1 0 0 1-1 1A17 17 0 0 1 3 4a1 1 0 0 1 1-1h3.5a1 1 0 0 1 1 1c0 1.25.2 2.45.57 3.57a1 1 0 0 1-.25 1z"/></svg>
        (555) 204-7731
      </li>
      <li>
        <svg viewBox="0 0 24 24" aria-hidden="true"><rect x="2" y="5" width="20" height="14" rx="2" fill="#f7941d"/><path d="M3 6l9 7 9-7" fill="none" stroke="#1f1f23" stroke-width="2"/></svg>
        hello@qal-vub.com
      </li>
      <li>
        <svg viewBox="0 0 24 24" aria-hidden="true"><circle cx="12" cy="12" r="10" fill="#f7941d"/><path d="M2 12h20M12 2c3 3 3 17 0 20M12 2c-3 3-3 17 0 20" fill="none" stroke="#1f1f23" stroke-width="1.6"/></svg>
        www.qal-vub.com
      </li>
    </ul>
  </div>

  <div class="address-band">4410 Harbor Pointe Dr. Suite 120 Mesa, AZ 85201</div>
</section>

</body>
</html>
```